Business card for my new company (Accounting firm)

I need a business card for my new business Brightwell Advisory and Ledger SA. Our services are accounting, tax, audit and financial management. Our customers are small companies, start-ups and new companies. The final design has to show financial security, trust and growth. Please find our logo attached to the business card. Text for the business card: Brightwell Advisory and Ledger SA Tomas Varenholt Director and Founder Certified Accountant Tel. 022 418 57 34 tv@clairevalconseil.ch www.clairevalconseil.ch Rue des Vergières 27 1201 Geneva
Target Market(s)
Our customers are small companies, start-ups and new companies.
Industry/Entity Type
Finance And Accounting
Contact Information for Business Card
Claireval Conseil et Comptes SA
Tomas Varenholt
Directeur et Fondateur
Expert-comptable diplômé
Tél. 022 418 57 34
tv@clairevalconseil.ch
www.clairevalconseil.ch
Rue des Vergières 27
1201 Genève

```html
<!DOCTYPE html>
<html lang="fr">
<head>
<meta charset="utf-8">
<title>Claireval Conseil et Comptes SA – Carte de visite</title>
<link rel="stylesheet" href="https://fonts.googleapis.com/css2?family=Montserrat:wght@600&family=Roboto:wght@400;700&display=swap">
<style>
  :root {
    --page: #d9dadc;
    --card-dark: #1e1f22;
    --emboss: #2c2d31;
    --blue: #2a8fc8;
    --blue-light: #2fa7dd;
    --blue-deep: #1c6fa6;
    --white: #ffffff;
  }
  * { box-sizing: border-box; margin: 0; padding: 0; }
  html, body {
    width: 799px; height: 1200px; overflow: hidden;
    background: var(--page);
  }
  .card {
    position: absolute; left: 90px;
    width: 620px; height: 354px;
    background: var(--card-dark);
    border-radius: 4px;
    overflow: hidden;
    box-shadow: 0 10px 24px rgba(0,0,0,.25);
  }
  .card--front { top: 150px; }
  .card--back { top: 690px; }

  /* Front */
  .front-name {
    position: absolute; left: 0; right: 0; top: 140px;
    text-align: center;
    font-family: "Montserrat", sans-serif; font-weight: 600;
    font-size: 30px; letter-spacing: 4px; line-height: 1.25;
    color: var(--emboss);
    text-transform: uppercase;
  }
  .front-stripe {
    position: absolute; left: 0; right: 0; bottom: 0; height: 12px;
    background: var(--blue-light);
  }

  /* Back */
  .back-name {
    position: absolute; right: 34px; top: 30px;
    text-align: right;
    font-family: "Montserrat", sans-serif; font-weight: 600;
    font-size: 24px; letter-spacing: 3px; line-height: 1.25;
    color: var(--white);
    text-transform: uppercase;
  }
  .back-band {
    position: absolute; left: 0; right: 0; top: 112px; height: 186px;
    background: linear-gradient(90deg, var(--blue-deep), var(--blue) 55%, var(--blue-light));
  }
  .contact {
    position: absolute; left: 36px; top: 126px;
    font-family: "Roboto", sans-serif; color: var(--white);
  }
  .contact__person { font-weight: 700; font-size: 22px; margin-bottom: 4px; }
  .contact__role { font-size: 13px; line-height: 1.35; }
  .contact__list { list-style: none; margin-top: 12px; }
  .contact__item {
    display: flex; align-items: center; gap: 10px;
    font-size: 15px; line-height: 1.6;
  }
  .contact__item svg { width: 13px; height: 13px; flex: none; }
  .address {
    position: absolute; left: 36px; bottom: 20px;
    font-family: "Roboto", sans-serif; font-size: 15px;
    color: var(--white);
  }
</style>
</head>
<body>

<section class="card card--front" aria-label="Recto">
  <p class="front-name">Claireval<br>Conseil et Comptes</p>
  <div class="front-stripe"></div>
</section>

<section class="card card--back" aria-label="Verso">
  <p class="back-name">Claireval<br>Conseil et Comptes</p>
  <div class="back-band"></div>
  <div class="contact">
    <p class="contact__person">Tomas Varenholt</p>
    <p class="contact__role">Directeur et Fondateur<br>Expert-comptable diplômé</p>
    <ul class="contact__list">
      <li class="contact__item">
        <svg viewBox="0 0 16 16" aria-hidden="true"><path fill="#fff" d="M3 1h3l1.5 4-2 1.3a9 9 0 0 0 4.2 4.2L11 8.5l4 1.5v3a2 2 0 0 1-2 2C7 15 1 9 1 3a2 2 0 0 1 2-2z"/></svg>
        022 418 57 34
      </li>
      <li class="contact__item">
        <svg viewBox="0 0 16 16" aria-hidden="true"><rect x="1" y="3" width="14" height="10" rx="1" fill="#fff"/><path d="M1.5 3.5 8 9l6.5-5.5" fill="none" stroke="#2a8fc8" stroke-width="1.3"/></svg>
        tv@clairevalconseil.ch
      </li>
      <li class="contact__item">
        <svg viewBox="0 0 16 16" aria-hidden="true"><g fill="none" stroke="#fff" stroke-width="1.4"><circle cx="8" cy="8" r="6.5"/><ellipse cx="8" cy="8" rx="2.8" ry="6.5"/><path d="M1.5 8h13"/></g></svg>
        www.clairevalconseil.ch
      </li>
    </ul>
  </div>
  <p class="address">Rue des Vergières 27 1201 Genève</p>
</section>

</body>
</html>
```